I need a SEO-friendly Wordpress website (making sure to style H1, H2, H3, etc correctly) for a Hawaii-based law firm called Meridian Crest Legal Group. Comparable websites include https://brvlaw.example/ and https://www.lomrit.example/ for design reference. The current copy on the TarnAdvocate.example website can be used.

```html
<!DOCTYPE html>
<html lang="en">
<head>
<meta charset="utf-8">
<title>Meridian Crest Legal Group</title>
<link href="https://fonts.googleapis.com/css2?family=Playfair+Display:wght@700&family=Poppins:wght@300;400;500&display=swap" rel="stylesheet">
<style>
:root{
  --orange:#c9791b;
  --orange-light:#dc9a3c;
  --brown:#7b2c08;
  --heading-brown:#8a3a10;
  --ink:#1a1a1a;
  --muted:#8a8a8a;
  --soft-bg:#f5f5f5;
  --white:#fff;
}
*{box-sizing:border-box;margin:0;padding:0}
html,body{width:1200px;height:3760px;overflow:hidden}
body{font-family:'Poppins',sans-serif;color:var(--ink);background:var(--white);position:relative}
.wrap{width:1046px;margin:0 auto;position:relative}
.band{position:relative;width:1200px}
.photo{display:block}
.btn{display:inline-flex;align-items:center;justify-content:center;border-radius:30px;background:linear-gradient(180deg,var(--orange-light),var(--orange));color:#fff;font-size:16px;font-weight:500}
.section-title{text-align:center;font-size:47px;font-weight:500;color:var(--ink)}
.section-title:after{content:"";display:block;width:156px;height:3px;background:var(--orange);margin:18px auto 0}

/* header */
.topline{height:6px;background:var(--orange)}
.site-header{height:108px}
.logo{position:absolute;left:0;top:28px;font-family:'Playfair Display',serif;font-size:38px;font-weight:700;color:#111}
.call{position:absolute;right:0;top:26px;display:flex;gap:16px;align-items:center}
.call small{display:block;font-size:14px;color:var(--orange)}
.call strong{font-size:23px;font-weight:400;color:var(--orange)}
.nav-band{height:73px;background:linear-gradient(180deg,var(--orange-light),var(--orange))}
.nav{display:flex;height:73px;align-items:center}
.nav a{color:#fff;font-size:15px;text-decoration:none;height:73px;display:flex;align-items:center}
.nav a.active{background:var(--brown);width:124px;justify-content:center;font-weight:500}
.nav .links{display:flex;gap:60px;margin-left:54px}
.search{position:absolute;right:0;top:17px;width:344px;height:40px;border-radius:20px;background:#fff;display:flex;align-items:center;justify-content:space-between;padding:0 16px;font-size:13px;color:#aaa}

/* hero */
.hero{height:573px;background:linear-gradient(90deg,#f1eeea 0%,#e4ded6 45%,#cfc7bd 100%)}
.hero-team{position:absolute;left:660px;top:40px;width:440px;height:533px;background:linear-gradient(180deg,#5c4f4a,#1f1f2a);z-index:1}
.hero-copy{position:absolute;left:79px;top:140px;width:570px;z-index:2}
.hero h1{font-size:38px;line-height:45px;font-weight:500;color:var(--heading-brown)}
.hero p{margin-top:22px;font-size:18.5px;line-height:31px;color:#333}
.hero .btn{margin-top:28px;width:228px;height:51px}

/* justice */
.justice{height:634px;background:var(--soft-bg);padding-top:68px}
.justice-photo{position:absolute;left:0;top:120px;width:522px;height:355px;background:#fff;box-shadow:0 2px 10px rgba(0,0,0,.15);padding:10px}
.justice-photo .photo{width:100%;height:100%;background:linear-gradient(135deg,#e8e4de,#8a8f97 60%,#3b3a3e)}
.justice-text{position:absolute;left:578px;top:122px;width:468px}
.justice-text h3{font-size:21px;line-height:31px;font-weight:400;color:var(--heading-brown)}
.justice-text p{margin-top:14px;font-size:12.5px;line-height:27px;color:var(--muted);font-weight:300}
.justice-text .btn{margin-top:30px;width:230px;height:52px;margin-left:-12px}

/* practice */
.practice{height:720px;padding-top:65px}
.cards{display:flex;gap:24px;margin-top:58px}
.card{width:333px}
.card .photo{height:218px}
.card h3{margin-top:24px;font-size:21px;font-weight:400;color:var(--heading-brown);padding-left:2px}
.card p{margin-top:12px;font-size:13px;line-height:23px;color:var(--muted);font-weight:300;padding-left:2px}
.card p span,.post p span{color:var(--orange);font-weight:400}
.view-all{display:flex;justify-content:center;margin-top:42px}
.view-all span{width:136px;height:51px;border:2px solid var(--brown);border-radius:26px;display:flex;align-items:center;justify-content:center;font-size:16px;color:var(--brown);font-weight:500}

/* consultant */
.consult{height:333px;background:linear-gradient(90deg,#2a2420,#3b332d 50%,#2a2622)}
.consult h2{position:absolute;left:2px;top:66px;font-size:47px;font-weight:500;color:#fff}
.consult p{position:absolute;left:2px;top:146px;width:720px;font-size:16.5px;line-height:29px;color:#fff}
.consult .btn{position:absolute;right:0;top:146px;width:229px;height:51px}

/* blog */
.blog{height:791px;padding-top:68px}
.posts{display:flex;gap:46px;margin-top:58px}
.post{width:500px}
.post .photo{height:333px}
.meta{display:flex;gap:34px;margin-top:26px;font-size:13px;color:#777;padding-left:2px}
.meta i{display:inline-block;width:12px;height:12px;background:var(--orange-light);border-radius:2px;margin-right:10px;vertical-align:-1px}
.post h3{margin-top:14px;font-size:19px;font-weight:400;color:var(--heading-brown);padding-left:2px}
.post p{margin-top:16px;font-size:12.5px;line-height:26px;color:var(--muted);font-weight:300;padding-left:2px}

/* newsletter */
.news{height:146px;background:linear-gradient(180deg,var(--orange-light),var(--orange))}
.news h2{position:absolute;left:2px;top:40px;font-size:28px;font-weight:400;color:#fff}
.news small{position:absolute;left:2px;top:86px;font-size:12.5px;color:#fff}
.news .field{position:absolute;left:478px;top:42px;width:396px;height:62px;border:1px solid #fff;color:#fff;font-size:13px;display:flex;align-items:center;padding-left:14px}
.news .submit{position:absolute;right:0;top:42px;width:161px;height:62px;background:var(--brown);color:#fff;font-size:16px;display:flex;align-items:center;justify-content:center}

/* footer */
.footer{height:314px;background:#fafafa}
.map{position:absolute;right:0;top:3384px;width:317px;height:376px;background:linear-gradient(135deg,#eeeae0,#e5e2d8 50%,#dcd8ca)}
.cols{position:absolute;left:79px;top:70px;display:flex}
.col{width:269px}
.col h4{font-size:21px;font-weight:400;color:#222}
.col ul{list-style:none;margin-top:26px}
.col li{font-size:13.5px;color:#888;line-height:31px;display:flex;align-items:flex-start;gap:14px}
.col li.dot:before{content:"";width:10px;height:10px;border-radius:50%;background:#bbb;margin-top:11px;flex:none}
.col li.on{color:var(--brown);font-weight:500}
.col li.on:before{background:var(--brown)}
.contact li{gap:18px;line-height:26px;margin-bottom:16px}
.contact svg{flex:none;margin-top:4px}
.bottom{position:absolute;left:0;top:3698px;width:883px;height:62px;background:linear-gradient(180deg,var(--orange-light),var(--orange))}
.bottom p{position:absolute;left:79px;top:23px;font-size:13px;color:#fff}
.social{position:absolute;left:654px;top:11px;display:flex;gap:12px}
.social span{width:41px;height:41px;border-radius:50%;background:#fff;display:block}
</style>
</head>
<body>
<div class="topline"></div>
<header class="band site-header">
  <div class="wrap">
    <div class="logo">Meridian Crest Legal Group</div>
    <div class="call">
      <svg width="42" height="50" viewBox="0 0 24 24"><path fill="#a8480f" d="M6.6 10.8a15.1 15.1 0 0 0 6.6 6.6l2.2-2.2c.3-.3.7-.4 1-.2 1.1.4 2.3.6 3.6.6.6 0 1 .4 1 1V20c0 .6-.4 1-1 1A17 17 0 0 1 3 4c0-.6.4-1 1-1h3.5c.6 0 1 .4 1 1 0 1.3.2 2.5.6 3.6.1.3 0 .7-.2 1z"/></svg>
      <div><small>Call Us Now</small><strong>+1.808.555.0142</strong></div>
    </div>
  </div>
</header>
<nav class="band nav-band">
  <div class="wrap nav">
    <a class="active">Home</a>
    <div class="links"><a>Practice Areas</a><a>Attorneys</a><a>Blog</a><a>Contact Us</a></div>
    <div class="search">Search here.....
      <svg width="20" height="20" viewBox="0 0 24 24"><circle cx="10" cy="10" r="7" fill="none" stroke="#222" stroke-width="2"/><path d="M15 15l6 6" stroke="#222" stroke-width="2"/></svg>
    </div>
  </div>
</nav>

<section class="band hero">
  <div class="hero-team photo" role="img" aria-label="Team of five attorneys in business suits in front of a courthouse"></div>
  <div class="hero-copy">
    <h1>Dedicated to making sure<br>you receive the care and<br>attention you need</h1>
    <p>Over 70 years of combined practice, specializing in:<br>Personal Injury, Family &amp; Divorce, Child Custody</p>
    <span class="btn">Free Consultant</span>
  </div>
</section>

<section class="band justice">
  <h2 class="section-title">Your Justice Is Our Priority</h2>
  <div class="wrap">
    <div class="justice-photo"><div class="photo" role="img" aria-label="Attorney meeting with clients over documents"></div></div>
    <div class="justice-text">
      <h3>Lawyers Serving the Big Island and Neighboring Islands</h3>
      <p>The experienced attorneys in the Meridian Crest Legal Group's Kailua Kona, Hawaii office provide clients with a wide range of litigation expertise, including legal claims involving divorce &amp; family, personal injury, toxic exposures, intellectual property, and real estate.</p>
      <p>Our Kona office also offers commercial and hospitality litigation expertise on behalf of a wide variety of clients, including restaurants, hotels, property owners, and many others.</p>
      <span class="btn">Learn More About Us</span>
    </div>
  </div>
</section>

<section class="band practice">
  <h2 class="section-title">Practice Areas</h2>
  <div class="wrap">
    <div class="cards">
      <article class="card"><div class="photo" role="img" aria-label="Parents arguing while their daughter sits at a table" style="background:linear-gradient(135deg,#e9e6e2,#b9aca0 60%,#6e5a4e)"></div>
        <h3>Family &amp; Divorce</h3><p>Our lawyers handle all aspects of family law on the Big Island and neighboring islands. We have more than 70 years of combined...<span>Read More</span></p></article>
      <article class="card"><div class="photo" role="img" aria-label="Injured man with arm sling working on a laptop" style="background:linear-gradient(135deg,#f0efed,#c9c4bc 55%,#5b6478)"></div>
        <h3>Personal Injury</h3><p>Dealing with personal injury and wrongful death claims is hard enough, so the lawyers of MCLG are here to make things...<span>Read More</span></p></article>
      <article class="card"><div class="photo" role="img" aria-label="Modern office building under a blue sky" style="background:linear-gradient(180deg,#5a7fb8,#a9bbd2 45%,#c8c8c2 75%,#6d7a52)"></div>
        <h3>Real Estate</h3><p>Our lawyers work with home owners, buyers and property developers to ensure timely handling of all legal aspects involved in real ...<span>Read More</span></p></article>
    </div>
    <div class="view-all"><span>View All</span></div>
  </div>
</section>

<section class="band consult" role="img" aria-label="Dark background of a gavel and scales of justice">
  <div class="wrap">
    <h2>Need A Consultant?</h2>
    <p>Lorem ipsum dolor sit amet, consectetur adipiscing elit, sed do eiusmod tempor incididunt ut labore et dolore magna aliqua. Ut enim ad minim veniam, quis nostrud exercitation ullamco laboris nisi ut aliquip ex ea commodo consequat. Duis aute irure dolor in reprehenderit in voluptate.</p>
    <span class="btn">Get A Free Quote</span>
  </div>
</section>

<section class="band blog">
  <h2 class="section-title">Recent Blog</h2>
  <div class="wrap">
    <div class="posts">
      <article class="post"><div class="photo" role="img" aria-label="Distressed woman sitting on the road after a car accident" style="background:linear-gradient(135deg,#4a4c50,#8e8f90 50%,#b9b7b2)"></div>
        <div class="meta"><span><i></i>July 30, 2019</span><span><i></i>0 Comments</span><span><i></i>Lee K.</span></div>
        <h3>Top 10 Things to Do Before Filing for Divorce</h3>
        <p>No one gets married with the intention of things not working out, but it's an unfortunate fact that many marriages don't work out in the end.&nbsp; For those who are in troubled marriage.... <span>Read More</span></p></article>
      <article class="post"><div class="photo" role="img" aria-label="Three colleagues reviewing a tablet at an office desk" style="background:linear-gradient(135deg,#c9b79c,#dcdad6 50%,#a8b4c6)"></div>
        <div class="meta"><span><i></i>July 30, 2019</span><span><i></i>0 Comments</span><span><i></i>Lee K.</span></div>
        <h3>Top 15 Things to Do During Custody Battle</h3>
        <p>It's already tragic enough when two people who planned on spending their lives together no longer wish to see that dream through, but to compound the tragedy is when children...<span>Read More</span></p></article>
    </div>
  </div>
</section>

<section class="band news">
  <div class="wrap">
    <h2>Get news directly to your email</h2>
    <small>we will only send your important updates and notices.</small>
    <div class="field">Your Email Address :</div>
    <div class="submit">Subcribe Now</div>
  </div>
</section>

<footer class="band footer">
  <div class="cols">
    <div class="col contact"><h4>Contact Us</h4>
      <ul>
        <li><svg width="20" height="20" viewBox="0 0 24 24"><path fill="#c9791b" d="M6.6 10.8a15.1 15.1 0 0 0 6.6 6.6l2.2-2.2c.3-.3.7-.4 1-.2 1.1.4 2.3.6 3.6.6.6 0 1 .4 1 1V20c0 .6-.4 1-1 1A17 17 0 0 1 3 4c0-.6.4-1 1-1h3.5c.6 0 1 .4 1 1 0 1.3.2 2.5.6 3.6.1.3 0 .7-.2 1z"/></svg>+1.808.555.0142</li>
        <li><svg width="20" height="16" viewBox="0 0 20 16"><rect width="20" height="16" rx="2" fill="#c9791b"/><path d="M1 2l9 7 9-7" stroke="#fff" stroke-width="1.6" fill="none"/></svg>clients@tarnadvocate.example</li>
        <li><svg width="18" height="22" viewBox="0 0 18 22"><path fill="#c9791b" d="M9 0a9 9 0 0 1 9 9c0 6-9 13-9 13S0 15 0 9a9 9 0 0 1 9-9z"/><circle cx="9" cy="9" r="3" fill="#fff"/></svg>18-204 Lanakila Road, Suite 310 Kailua Kona, Hawaii 96740</li>
      </ul></div>
    <div class="col"><h4>Quick Links</h4>
      <ul><li class="dot on">Home</li><li class="dot">Practice Areas</li><li class="dot">Attorneys</li><li class="dot">Blog</li><li class="dot">Contact</li></ul></div>
    <div class="col"><h4>Practice Areas</h4>
      <ul><li class="dot">Family &amp; Divorce</li><li class="dot">Personal Injury</li><li class="dot">Corporate &amp; IP</li><li class="dot">Real Estate</li></ul></div>
  </div>
</footer>
<div class="map" role="img" aria-label="Street map showing the office location"></div>
<div class="bottom">
  <p>Copyright © Meridian Crest Legal Group. All Rights Reserved.</p>
  <div class="social"><span aria-label="Social profile"></span><span aria-label="Social profile"></span><span aria-label="Social profile"></span><span aria-label="Social profile"></span></div>
</div>
</body>
</html>
```